Velvet Lantern rebranding my business with a new business card

I have my new logo and now I need a refresher on my business cards. I really want something fun and fresh. I like black background or anything to make the color pop.
Logo
Name: Velvet Lantern
Contact Info as stated below:
Mira Pellow
555-013-4762
Logo
Name: Velvet Lantern
Mira Pellow
555-013-4762
fb.me/VelvetLanternbyMira
Instagram: @VelvetLanternbyMira

Industry/Entity Type

Business

Contact Information for Business Card

double-sided. Logo on one side. Contact info on the other.

Requirements
Must have
• Logo
• Name: Velvet Lantern
• Contact Info as stated below:
• Mira Pellow
• 555-013-4762
• fb.me/VelvetLanternbyMira
• fb.me/VelvetLanternbyMira

```html
<!DOCTYPE html>
<html lang="en">
<head>
<meta charset="utf-8">
<title>Velvet Lantern – Business Card</title>
<link rel="stylesheet" href="https://fonts.googleapis.com/css2?family=Comic+Neue:wght@400;700&display=swap">
<style>
  :root {
    --backdrop: #e4e4e4;
    --blush: #f4b9bc;
    --blush-deep: #e88f9e;
    --ring-pink: #ee9fb0;
    --card-white: #f7f7f7;
    --ink: #1d1d1d;
    --icon-plum: #a45b94;
    --icon-fill: #f6dbe9;
    --shadow: rgba(0, 0, 0, 0.28);
  }
  * { box-sizing: border-box; margin: 0; padding: 0; }
  html, body {
    width: 1200px; height: 576px; overflow: hidden;
    background: var(--backdrop);
    font-family: "Comic Neue", "Trebuchet MS", sans-serif;
    color: var(--ink);
  }
  .canvas { position: relative; width: 1200px; height: 576px; }

  .card {
    position: absolute; top: 138px;
    width: 484px; height: 294px;
    border-radius: 12px; overflow: hidden;
    box-shadow: 2px 4px 8px var(--shadow);
  }

  /* Brand lockup: name with one plain dot */
  .brand {
    display: flex; align-items: center; gap: 10px;
  }
  .brand__dot {
    flex: none; width: 34px; height: 34px; border-radius: 50%;
    background: var(--blush-deep);
  }
  .brand__name {
    font-weight: 700; font-size: 30px; color: var(--ink);
    line-height: 1.05; text-align: left;
  }

  /* Front: logo side */
  .card--front { left: 82px; background: var(--blush); }
  .front__seal {
    position: absolute; left: 138px; top: 43px;
    width: 208px; height: 208px; border-radius: 50%;
    background: #fff;
    border: 2px solid var(--ink);
    box-shadow: inset 0 0 0 5px #fff, inset 0 0 0 7px var(--ring-pink);
    display: flex; align-items: center; justify-content: center;
  }

  /* Back: contact side */
  .card--back { left: 602px; width: 482px; height: 292px; background: var(--card-white); }
  .back__brand {
    position: absolute; left: 0; right: 0; top: 50px; height: 130px;
    display: flex; align-items: center; justify-content: center;
  }
  .back__brand .brand__dot { width: 44px; height: 44px; }
  .back__brand .brand__name { font-size: 36px; }
  .back__band { position: absolute; left: 0; top: 0; width: 482px; height: 292px; }
  .contact {
    position: absolute; left: 70px; top: 226px;
    display: flex; align-items: center; gap: 16px;
  }
  .contact__name { font-size: 25px; font-weight: 400; }
  .contact__list { list-style: none; display: flex; flex-direction: column; gap: 6px; }
  .contact__item { display: flex; align-items: center; gap: 8px; font-size: 18px; line-height: 1; }
  .contact__icon {
    width: 17px; height: 17px; border-radius: 3px;
    background: var(--icon-fill); border: 1.5px solid var(--icon-plum);
    display: inline-flex; align-items: center; justify-content: center;
  }
</style>
</head>
<body>
<main class="canvas">

  <section class="card card--front" aria-label="Business card front">
    <div class="front__seal">
      <div class="brand">
        <span class="brand__dot"></span>
        <span class="brand__name">Velvet<br>Lantern</span>
      </div>
    </div>
  </section>

  <section class="card card--back" aria-label="Business card back">
    <div class="back__brand">
      <div class="brand">
        <span class="brand__dot"></span>
        <span class="brand__name">Velvet<br>Lantern</span>
      </div>
    </div>

    <svg class="back__band" viewBox="0 0 482 292" aria-hidden="true">
      <path d="M0 234 Q241 160 482 234 L482 292 L0 292 Z" fill="var(--blush)"/>
      <path d="M0 236 Q241 150 482 236 Q241 164 0 236 Z" fill="var(--ink)"/>
    </svg>

    <div class="contact">
      <span class="contact__name">Mira Pellow</span>
      <ul class="contact__list">
        <li class="contact__item">
          <span class="contact__icon">
            <svg width="10" height="10" viewBox="0 0 24 24" aria-hidden="true">
              <path fill="var(--icon-plum)" d="M6.6 10.8a15.1 15.1 0 0 0 6.6 6.6l2.2-2.2c.3-.3.7-.4 1-.2 1.1.4 2.3.6 3.6.6.6 0 1 .4 1 1V20c0 .6-.4 1-1 1A17 17 0 0 1 3 4c0-.6.4-1 1-1h3.5c.6 0 1 .4 1 1 0 1.3.2 2.5.6 3.6.1.3 0 .7-.2 1z"/>
            </svg>
          </span>
          555-013-4762
        </li>
        <li class="contact__item">
          <span class="contact__icon"></span>
          VelvetLanternbyMira
        </li>
      </ul>
    </div>
  </section>

</main>
</body>
</html>
```